eCommerce Website Design for Children's Book Service

I am looking for a 5 page eCommerce website that includes a Shopping Cart. 'Lumiva Books' is the title of the company and its logo is attached. 'Sprouting wonder in words,' is the company's motto and 'spring green' is the main color. The website needs to appeal to families. Images of books and/or maple seeds (helicopter seeds) moving are part of the graphics.
Updates

I have updated my brief and I would like my website design to include 5 pages: home, about, products (books), blog, contact. WordPress is the web format that I am most comfortable with.

Target Market(s)

Families with young children

Coding

Coded - Design and coding required

Number of Pages Required

5+ page

Requirements
Must have
• Shopping cart page; contact page, books page with spaces of photos to go, blog page; spring green color
Nice to have
• A graphic that relates to motto : "sprouting wonder in words"
• WordPress

```html
<!DOCTYPE html>
<html lang="en">
<head>
<meta charset="utf-8">
<title>Lumiva Books — Sprouting Wonder in Words</title>
<link href="https://fonts.googleapis.com/css2?family=Josefin+Sans:wght@400;600;700&family=Montserrat:wght@400;500;600;700&display=swap" rel="stylesheet">
<style>
:root{
  --green:#1fa83a;
  --green-dark:#128a2c;
  --green-deep:#0d7a25;
  --teal:#1e6a6d;
  --teal-dark:#164f55;
  --ink:#222;
  --muted:#777;
  --line:#e3e3e3;
  --footer:#1f1f1f;
  --star:#f2b01e;
  --white:#fff;
}
*{box-sizing:border-box;margin:0;padding:0}
html,body{width:1200px;height:4072px;overflow:hidden}
body{position:relative;font-family:"Montserrat",sans-serif;color:var(--ink);background:var(--white)}
.abs{position:absolute}
h1,h2,.logo-name{font-family:"Josefin Sans",sans-serif}

/* top bar */
.topbar{left:0;top:0;width:1200px;height:33px;background:var(--green);color:#fff;font-size:11px;font-weight:600}
.topbar .contact{left:174px;top:10px}
.topbar .account{right:200px;top:10px}
.navbar{left:0;top:33px;width:1200px;height:95px;background:#fff}
.logo{left:180px;top:20px;width:190px;height:180px;border-radius:50%;background:#fff;display:flex;align-items:center;justify-content:center;box-shadow:0 6px 14px rgba(0,0,0,.08);z-index:3}
.logo-name{font-size:30px;font-weight:600;color:var(--green-dark)}
.menu{left:538px;top:72px;display:flex;gap:30px;font-size:15px;font-weight:500}
.menu .active{color:var(--green)}
.cart{left:976px;top:66px}

/* hero */
.hero{left:0;top:128px;width:1200px;height:660px;background:linear-gradient(100deg,#ece9e4 0%,#dcd6cc 45%,#b9a993 80%,#a89780 100%)}
.hero-photo{left:600px;top:0;width:600px;height:600px;background:radial-gradient(ellipse at 55% 50%,#c9ae8b 0%,#b59d82 35%,rgba(181,157,130,0) 70%)}
.hero h1{left:174px;top:150px;font-size:62px;line-height:1.1;font-weight:600;color:#222}
.hero .sub{left:174px;top:312px;font-size:16px;color:#333}
.btn{display:inline-block;background:var(--green);color:#fff;font-weight:700;font-size:15px;border-radius:30px;text-align:center}
.hero .btn{left:174px;top:361px;width:163px;height:46px;line-height:46px}
.dots{left:174px;top:466px;display:flex;gap:6px}
.dots i{width:9px;height:9px;border-radius:50%;background:#bbb;display:block}
.dots i:first-child{background:#999}
.arrow-dark{width:40px;height:40px;border-radius:50%;background:#3a3a3a;display:flex;align-items:center;justify-content:center}
.hero-wave{left:0;top:650px;width:1200px;height:145px}

/* section titles */
.title{left:0;width:1200px;display:flex;justify-content:center;align-items:center;gap:22px}
.title h2{font-size:36px;font-weight:600}
.title .bar{width:52px;height:3px;background:var(--green)}

.tabs{left:437px;top:958px;display:flex;gap:12px}
.tab{height:38px;line-height:38px;padding:0 20px;border:1px solid var(--line);font-size:12px;font-weight:600;color:#444}
.tab.on{background:var(--green);color:#fff;border-color:var(--green)}

.card{background:#fff;border:1px solid var(--line)}
.card.lift{border:2px solid #bfe3c6;box-shadow:0 6px 16px rgba(0,0,0,.08)}
.card .img{position:absolute;inset:20px;border-radius:4px}
.pname{text-align:center;font-size:17px;font-weight:600}
.price{text-align:center;font-size:17px;font-weight:700;color:var(--green)}
.stars{color:var(--star);font-size:14px;letter-spacing:1px;text-align:center}
.ribbon{width:22px;height:46px;background:var(--green);clip-path:polygon(0 0,100% 0,100% 100%,50% 80%,0 100%)}
.ribbon.sale{background:#e8553f}
.arrow-ring{width:40px;height:40px;border-radius:50%;border:1.5px solid #999;display:flex;align-items:center;justify-content:center;background:#fff}
.actions{display:flex;gap:10px}
.actions i{width:30px;height:30px;border-radius:50%;background:var(--green);display:block;border:2px solid #fff}

/* about */
.about{left:0;top:1420px;width:1200px;height:580px}
.about h2{left:684px;top:1540px;font-size:36px;color:#fff;font-weight:600;display:flex;align-items:center;gap:18px}
.about h2 .bar{width:48px;height:3px;background:var(--green);display:block}
.about-text{left:684px;top:1600px;width:360px;font-size:13.5px;line-height:27px;color:#e6f0ef}
.about .btn{left:684px;top:1797px;width:158px;height:48px;line-height:48px}

/* testimonials */
.testi{left:0;top:2550px;width:1200px;height:590px}
.quote{width:295px;display:flex;gap:18px}
.avatar{width:62px;height:62px;border-radius:50%;border:3px solid #fff;background:linear-gradient(135deg,#d9c3b0,#9c8472);flex:none}
.quote p{font-size:11px;line-height:17px;color:#fff;font-style:italic;font-weight:500}
.quote .who{font-size:9.5px;font-weight:700;color:#fff;margin-top:8px}
.quote .role{font-size:9px;color:#dff2e2}
.quote .stars{text-align:left;margin-top:14px;font-size:17px}
.arrow-light{width:34px;height:34px;border-radius:50%;border:1.5px solid rgba(255,255,255,.8);display:flex;align-items:center;justify-content:center}

/* blog */
.post{width:256px;height:312px;background:#fff;box-shadow:0 4px 14px rgba(0,0,0,.1);padding:14px 14px 0}
.post .img{height:135px}
.post h3{font-size:14.5px;font-weight:600;margin-top:16px}
.post .meta{font-size:10px;color:#888;margin-top:12px;display:flex;gap:16px}
.post .meta b{color:var(--green)}
.post p{font-size:11px;line-height:17px;color:#777;margin-top:10px}

/* footer */
.footer{left:0;top:3590px;width:1200px;height:482px}
.kids{left:54px;top:3590px;width:260px;height:200px;border-radius:40% 40% 10% 10%;background:linear-gradient(160deg,#e68a3a,#d44b3e 50%,#3b7fc4)}
.f-contact{top:3838px;display:flex;align-items:center;gap:14px;color:#fff;font-size:13px;font-weight:600;line-height:18px}
.f-icon{width:34px;height:34px;border-radius:50%;border:1.5px solid #fff;display:flex;align-items:center;justify-content:center;flex:none}
.f-menu{left:0;width:1200px;top:3920px;display:flex;justify-content:center;gap:30px;color:#fff;font-size:14px;font-weight:600}
.f-copy{left:0;width:1200px;top:3960px;text-align:center;color:#bbb;font-size:11px}
.social{left:0;width:1200px;top:4006px;display:flex;justify-content:center;gap:10px}
.social i{width:28px;height:28px;border-radius:50%;display:block}
</style>
</head>
<body>

<!-- top bar -->
<div class="abs topbar">
  <div class="abs contact">&#9742; Phone : 1 888 888 8888 &nbsp;|&nbsp; &#9993; Email : info@companyname.com</div>
  <div class="abs account">&#128274; Login &nbsp;|&nbsp; &#9787; My Account</div>
</div>

<!-- hero -->
<section class="abs hero" role="img" aria-label="Photo of a young girl in glasses reading on a stack of books">
  <div class="abs hero-photo"></div>
</section>
<div class="abs hero" style="background:none">
  <h1 class="abs">Sprouting<br>Wonder in Words</h1>
  <div class="abs sub">Lorem Ipsum is simply dummy text of the</div>
  <a class="abs btn">SHOP NOW</a>
  <div class="abs dots"><i></i><i></i><i></i><i></i><i></i></div>
  <div class="abs arrow-dark" style="left:45px;top:300px"><svg width="12" height="12" viewBox="0 0 12 12"><path d="M8 1 3 6l5 5" stroke="#fff" stroke-width="2" fill="none"/></svg></div>
  <div class="abs arrow-dark" style="left:1114px;top:300px"><svg width="12" height="12" viewBox="0 0 12 12"><path d="M4 1l5 5-5 5" stroke="#fff" stroke-width="2" fill="none"/></svg></div>
</div>
<svg class="abs hero-wave" viewBox="0 0 1200 145" preserveAspectRatio="none">
  <path d="M0 30 C200 110 420 120 600 80 C780 120 1000 110 1200 30 L1200 145 L0 145Z" fill="#fff"/>
  <path d="M0 30 C200 110 420 120 600 80 C780 120 1000 110 1200 30" stroke="var(--green)" stroke-width="5" fill="none"/>
  <path d="M540 98 L600 40 L660 98 Z" fill="#fff" stroke="var(--green)" stroke-width="4"/>
</svg>

<!-- nav -->
<header class="abs navbar">
  <div class="abs menu"><span class="active">Home</span><span>About us</span><span>Products</span><span>News</span><span>Contact us</span></div>
  <div class="abs cart"><svg width="36" height="30" viewBox="0 0 36 30"><path d="M2 4h6l4 16h16l4-11H10" stroke="#555" stroke-width="2.5" fill="none"/><circle cx="14" cy="25" r="2.5" fill="#555"/><circle cx="26" cy="25" r="2.5" fill="#555"/><circle cx="30" cy="5" r="6" fill="var(--green)"/><text x="30" y="8" font-size="8" fill="#fff" text-anchor="middle" font-family="Montserrat,sans-serif">0</text></svg></div>
</header>
<div class="abs logo"><span class="logo-name">Lumiva Books</span></div>

<!-- most popular -->
<div class="abs title" style="top:872px"><span class="bar"></span><h2>Most Popular</h2><span class="bar"></span></div>
<div class="abs tabs"><span class="tab on">All</span><span class="tab">FEATURED</span><span class="tab">POPULAR</span></div>

<div class="abs arrow-ring" style="left:106px;top:1161px"><svg width="10" height="10" viewBox="0 0 10 10"><path d="M7 1 3 5l4 4" stroke="#555" stroke-width="1.8" fill="none"/></svg></div>
<div class="abs arrow-ring" style="left:1052px;top:1161px"><svg width="10" height="10" viewBox="0 0 10 10"><path d="M3 1l4 4-4 4" stroke="#555" stroke-width="1.8" fill="none"/></svg></div>

<div class="abs card" style="left:185px;top:1078px;width:244px;height:239px"><div class="img" role="img" aria-label="Photo of an open book on a small stack" style="background:linear-gradient(160deg,#f4f1ea,#cbb89a)"></div></div>
<div class="abs ribbon sale" style="left:214px;top:1078px"></div>
<div class="abs pname" style="left:185px;top:1334px;width:244px">Product Name</div>
<div class="abs price" style="left:185px;top:1366px;width:244px">$56.8</div>

<div class="abs card lift" style="left:478px;top:1050px;width:244px;height:252px"><div class="img" role="img" aria-label="Photo of a tall stack of colourful books" style="background:linear-gradient(170deg,#d7dfe8,#b34c43 45%,#3d6e99)"></div></div>
<div class="abs actions" style="left:550px;top:1168px"><i></i><i></i><i></i></div>
<div class="abs pname" style="left:478px;top:1318px;width:244px">Product Name</div>
<div class="abs price" style="left:478px;top:1350px;width:244px">$56.8</div>
<div class="abs stars" style="left:478px;top:1376px;width:244px">★★★★★</div>

<div class="abs card" style="left:771px;top:1078px;width:244px;height:239px"><div class="img" role="img" aria-label="Photo of a red apple on a stack of books" style="background:linear-gradient(170deg,#f3f3f0,#d23a2e 40%,#5a7a9a)"></div></div>
<div class="abs ribbon" style="left:800px;top:1078px"></div>
<div class="abs pname" style="left:771px;top:1334px;width:244px">Product Name</div>
<div class="abs price" style="left:771px;top:1366px;width:244px">$56.8</div>

<!-- about -->
<svg class="abs about" viewBox="0 0 1200 580" preserveAspectRatio="none" role="img" aria-label="Photo of open books on a teal chalkboard background with paper birds">
  <defs><linearGradient id="aboutBg" x1="0" y1="0" x2="1" y2="1"><stop offset="0" stop-color="#2c7f80"/><stop offset="1" stop-color="var(--teal-dark)"/></linearGradient>
  <linearGradient id="bookBg" x1="0" y1="0" x2="1" y2="0"><stop offset="0" stop-color="#c25a2a"/><stop offset=".5" stop-color="#e9e3d6"/><stop offset="1" stop-color="#5f7d86"/></linearGradient></defs>
  <path d="M0 120 C250 10 450 140 700 80 C900 30 1050 20 1200 60 L1200 500 C1000 560 800 470 600 520 C400 570 200 540 0 470Z" fill="url(#aboutBg)"/>
  <path d="M0 420 C150 330 400 340 620 420 L620 560 C400 560 200 540 0 520Z" fill="url(#bookBg)" opacity=".85"/>
</svg>
<h2 class="abs about" style="left:684px;top:1540px;width:auto;height:auto;font-size:36px;color:#fff;font-weight:600;display:flex;align-items:center;gap:18px"><span class="bar" style="width:48px;height:3px;background:var(--green)"></span>About us<span class="bar" style="width:48px;height:3px;background:var(--green)"></span></h2>
<p class="abs about-text">Lorem Ipsum is simply dummy text of the printing and typesetting industry. Lorem Ipsum has been the industry's standard dummy text ever since the 1500s, when an unknown printer took a galley of type and scrambled it to make a type specimen but also the leap into electronic typesetting, remaining essentially.</p>
<a class="abs btn" style="left:684px;top:1797px;width:158px;height:48px;line-height:48px">READ MORE</a>

<!-- featured products -->
<div class="abs title" style="top:2090px"><span class="bar"></span><h2>Featured Products</h2><span class="bar"></span></div>
<div class="abs arrow-ring" style="left:106px;top:2290px"><svg width="10" height="10" viewBox="0 0 10 10"><path d="M7 1 3 5l4 4" stroke="#555" stroke-width="1.8" fill="none"/></svg></div>
<div class="abs arrow-ring" style="left:1052px;top:2290px"><svg width="10" height="10" viewBox="0 0 10 10"><path d="M3 1l4 4-4 4" stroke="#555" stroke-width="1.8" fill="none"/></svg></div>

<div class="abs card" style="left:174px;top:2208px;width:201px;height:222px"><div class="img" role="img" aria-label="Photo of a stack of coloured books" style="background:linear-gradient(180deg,#f6f6f3,#e0b33a 35%,#c33d3a 60%,#2f7a5e)"></div></div>
<div class="abs ribbon sale" style="left:186px;top:2208px"></div>
<div class="abs pname" style="left:174px;top:2460px;width:201px">Product Name</div>
<div class="abs price" style="left:174px;top:2493px;width:201px">$56.8</div>

<div class="abs card lift" style="left:391px;top:2194px;width:201px;height:236px"><div class="img" role="img" aria-label="Photo of a stack of hardcover books" style="background:linear-gradient(180deg,#f3f3f0,#a8423c 40%,#3a5f88)"></div></div>
<div class="abs actions" style="left:444px;top:2296px"><i></i><i></i><i></i></div>
<div class="abs pname" style="left:391px;top:2446px;width:201px">Product Name</div>
<div class="abs price" style="left:391px;top:2478px;width:201px">$56.8</div>
<div class="abs stars" style="left:391px;top:2504px;width:201px">★★★★★</div>

<div class="abs card" style="left:608px;top:2208px;width:201px;height:222px"><div class="img" role="img" aria-label="Photo of a leaning pile of books" style="background:linear-gradient(180deg,#f6f6f3,#5b8b5c 40%,#b0463a)"></div></div>
<div class="abs ribbon" style="left:620px;top:2208px"></div>
<div class="abs pname" style="left:608px;top:2460px;width:201px">Product Name</div>
<div class="abs price" style="left:608px;top:2493px;width:201px">$56.8</div>

<div class="abs card" style="left:825px;top:2194px;width:201px;height:236px"><div class="img" role="img" aria-label="Photo of a neat stack of old books" style="background:linear-gradient(180deg,#f6f6f3,#8b6a4e 40%,#6e3a30)"></div></div>
<div class="abs pname" style="left:825px;top:2446px;width:201px">Product Name</div>
<div class="abs price" style="left:825px;top:2478px;width:201px">$56.8</div>

<!-- testimonials -->
<svg class="abs testi" viewBox="0 0 1200 590" preserveAspectRatio="none">
  <path d="M0 80 C250 0 500 60 700 40 C900 20 1050 0 1200 40 L1200 480 C1000 590 750 600 600 560 C400 510 200 470 0 520Z" fill="var(--green)"/>
  <path d="M0 450 C200 420 400 470 600 520 C750 560 1000 540 1200 460 L1200 480 C1000 590 750 600 600 560 C400 510 200 470 0 520Z" fill="var(--green-deep)"/>
</svg>
<div class="abs title" style="top:2704px"><span class="bar" style="background:#fff"></span><h2 style="color:#fff">Testimonials</h2><span class="bar" style="background:#fff"></span></div>
<div class="abs arrow-light" style="left:100px;top:2860px"><svg width="10" height="10" viewBox="0 0 10 10"><path d="M7 1 3 5l4 4" stroke="#fff" stroke-width="1.8" fill="none"/></svg></div>
<div class="abs arrow-light" style="left:1066px;top:2860px"><svg width="10" height="10" viewBox="0 0 10 10"><path d="M3 1l4 4-4 4" stroke="#fff" stroke-width="1.8" fill="none"/></svg></div>

<div class="abs quote" style="left:160px;top:2815px">
  <div class="avatar" role="img" aria-label="Customer portrait"></div>
  <div><p>&ldquo; At vero eos et accusamus et iusto odio dignissimos ducimus qui blanditiis praesentium deleniti atq.</p><div class="who">NORA BLAKE</div><div class="role">Financial Services Professional</div><div class="stars">★★★★☆</div></div>
</div>
<div class="abs quote" style="left:465px;top:2815px">
  <div class="avatar" role="img" aria-label="Customer portrait"></div>
  <div><p>&ldquo; At vero eos et accusamus et iusto odio dignissimos ducimus qui blanditiis praesentium voluptatum.</p><div class="who">OWEN HARTLEY</div><div class="role">National Urban Fellow at the Theater</div><div class="stars">★★★★½</div></div>
</div>
<div class="abs quote" style="left:770px;top:2815px">
  <div class="avatar" role="img" aria-label="Customer portrait"></div>
  <div><p>&ldquo; At vero eos et accusamus et iusto odio dignissimos ducimus qui blanditiis praesentium voluptatum.</p><div class="who">PRIYA SOLEN</div><div class="role">Creative Strategist | Entrepreneur</div><div class="stars">★★★★☆</div></div>
</div>

<!-- blog -->
<div class="abs title" style="top:3174px"><span class="bar"></span><h2>Testimonials</h2><span class="bar"></span></div>
<div class="abs arrow-ring" style="left:106px;top:3398px;width:34px;height:34px;border-color:#ccc"><svg width="10" height="10" viewBox="0 0 10 10"><path d="M7 1 3 5l4 4" stroke="#bbb" stroke-width="1.8" fill="none"/></svg></div>
<div class="abs arrow-ring" style="left:1060px;top:3398px;width:34px;height:34px;border-color:#ccc"><svg width="10" height="10" viewBox="0 0 10 10"><path d="M3 1l4 4-4 4" stroke="#bbb" stroke-width="1.8" fill="none"/></svg></div>

<article class="abs post" style="left:174px;top:3258px">
  <div class="img" role="img" aria-label="Photo of a child writing at a desk" style="background:linear-gradient(160deg,#e9e4dc,#b48e6c)"></div>
  <h3>Sed ut perspiciatis unde error</h3>
  <div class="meta"><span><b>&#9635;</b> 03 March 2016</span><span><b>&#9719;</b> 04:50</span></div>
  <p>Sed ut perspiciatis unde omnis iste natus error sit voluptatem accusantium doloremque laudantium</p>
</article>
<article class="abs post" style="left:472px;top:3258px">
  <div class="img" role="img" aria-label="Photo of a girl reading a glowing book" style="background:linear-gradient(160deg,#b8281e,#e7a63c 55%,#5a1a12)"></div>
  <h3>Sed ut perspiciatis unde error</h3>
  <div class="meta"><span><b>&#9635;</b> 03 March 2016</span><span><b>&#9719;</b> 04:50</span></div>
  <p>Sed ut perspiciatis unde omnis iste natus error sit voluptatem accusantium doloremque laudantium</p>
</article>
<article class="abs post" style="left:770px;top:3258px">
  <div class="img" role="img" aria-label="Photo of a child sitting on a stack of books" style="background:linear-gradient(160deg,#f0ece6,#cbb59a)"></div>
  <h3>Sed ut perspiciatis unde error</h3>
  <div class="meta"><span><b>&#9635;</b> 03 March 2016</span><span><b>&#9719;</b> 04:50</span></div>
  <p>Sed ut perspiciatis unde omnis iste natus error sit voluptatem accusantium doloremque laudantium</p>
</article>

<!-- footer -->
<svg class="abs footer" viewBox="0 0 1200 482" preserveAspectRatio="none">
  <path d="M0 130 C300 210 700 160 1200 60 L1200 482 L0 482Z" fill="var(--green)"/>
  <path d="M0 145 C300 225 700 178 1200 78 L1200 482 L0 482Z" fill="var(--footer)"/>
</svg>
<div class="abs kids" role="img" aria-label="Illustration of children reading around a pile of books and a globe"></div>

<div class="abs f-contact" style="left:245px">
  <span class="f-icon"><svg width="14" height="16" viewBox="0 0 14 16"><path d="M7 1a5 5 0 0 1 5 5c0 4-5 9-5 9S2 10 2 6a5 5 0 0 1 5-5z" stroke="#fff" stroke-width="1.6" fill="none"/><circle cx="7" cy="6" r="1.8" fill="#fff"/></svg></span>
  <span>333,Sed ut perspiciatis unde<br>omnis iste natus error</span>
</div>
<div class="abs f-contact" style="left:520px;top:3846px">
  <span class="f-icon"><svg width="14" height="14" viewBox="0 0 14 14"><path d="M3 1l2.5 3-1.5 1.5c.8 1.8 2.2 3.2 4 4L9.5 8l3 2.5L11 13C6 13 1 8 1 3z" fill="#fff"/></svg></span>
  <span>1 888 888 8888</span>
</div>
<div class="abs f-contact" style="left:705px;top:3846px">
  <span class="f-icon"><svg width="14" height="12" viewBox="0 0 14 12"><rect x="1" y="1" width="12" height="10" stroke="#fff" stroke-width="1.5" fill="none"/><path d="M1 1l6 5 6-5" stroke="#fff" stroke-width="1.5" fill="none"/></svg></span>
  <span>Email: info@companyname.com</span>
</div>
<nav class="abs f-menu"><span>Home</span><span>About us</span><span>Products</span><span>News</span><span>Contact us</span><span>My Account</span></nav>
<div class="abs f-copy">Copyright © 2019, Companyname All Rights Reserved &nbsp;|&nbsp; Privacy Policy</div>
<div class="abs social"><i style="background:#3b5998"></i><i style="background:#1da1f2"></i><i style="background:#d93a2e"></i><i style="background:#c58a2e"></i></div>

</body>
</html>
```